Verlindo Magician

I want the business card for my business to give to people who watch that later I will be employed to show magic here is my website http://www.verlindoillusions.example/I want the interesting design , i am very opened for formal and informal, I watch a lot of design so don't stick to the common shape and form but i hope it can also be produced the thing to write on will be the same as in picture that i will upload , i also will upload the logo for you that so can be easy to useDenis CostilleMagicianMAGICIAN VERLINDO 17 rue des Tilleuls - 25000 BESANÇON contact@verlindoillusions.example tel. 0381 946 157 tel. 0674 219 503

```html
<!DOCTYPE html>
<html lang="fr">
<head>
<meta charset="utf-8">
<title>Verlindo Magician – Business Card</title>
<link rel="stylesheet" href="https://fonts.googleapis.com/css2?family=Jost:wght@300;400&family=Lato:wght@400;700&display=swap">
<style>
  :root {
    --page-bg: #ebebeb;
    --card-bg: #ffffff;
    --brand-red: #b3363a;
    --ink: #111111;
    --text: #333333;
    --white: #ffffff;
  }
  * { box-sizing: border-box; margin: 0; padding: 0; }
  html, body {
    width: 1200px; height: 800px; overflow: hidden;
    background: var(--page-bg);
  }
  .canvas { position: relative; width: 1200px; height: 800px; }

  .card {
    position: absolute; left: 312px;
    width: 584px; height: 338px;
    background: var(--card-bg);
    border-radius: 18px;
    overflow: hidden;
  }
  .card--front { top: 46px; }
  .card--back { top: 417px; }

  /* front */
  .band { position: absolute; left: 0; right: 0; background: var(--brand-red); }
  .band--top { top: 0; height: 73px; }
  .band--bottom { bottom: 0; height: 54px; }

  .portrait {
    position: absolute; background: var(--ink);
  }
  .card--front .portrait {
    left: 0; top: 24px; width: 264px; height: 314px;
    border-radius: 120px 120px 0 0;
  }
  .card--back .portrait {
    left: 198px; top: 29px; width: 180px; height: 223px;
    border-radius: 90px 90px 20px 20px;
  }

  .wordmark {
    position: absolute; text-align: center;
    font-family: "Jost", sans-serif; font-weight: 300;
    letter-spacing: 0.5px; line-height: 1;
  }
  .wordmark__name { display: block; font-size: 38px; }
  .wordmark__sub { display: block; font-size: 11px; letter-spacing: 0.5px; margin-top: 4px; }
  .card--front .wordmark { left: 286px; width: 200px; top: 14px; color: var(--white); }
  .card--back .wordmark { left: 188px; width: 200px; top: 256px; color: var(--ink); }

  .person { position: absolute; left: 303px; top: 100px; font-family: "Lato", sans-serif; }
  .person__name { font-size: 21px; font-weight: 400; color: var(--brand-red); letter-spacing: 0.2px; }
  .person__role { font-size: 14px; font-weight: 700; color: var(--ink); margin-top: 8px; letter-spacing: 0.3px; }

  .contacts {
    position: absolute; left: 303px; top: 175px;
    list-style: none;
    font-family: "Jost", sans-serif; font-weight: 400;
    font-size: 14px; color: var(--text);
  }
  .contacts li { display: flex; align-items: center; height: 24px; }
  .contacts svg { width: 13px; height: 13px; margin-right: 9px; fill: var(--brand-red); flex: none; }

  .address {
    position: absolute; left: 303px; bottom: 8px;
    font-family: "Jost", sans-serif; font-weight: 400;
    font-size: 13.5px; line-height: 17px; color: var(--white);
  }
</style>
</head>
<body>
<main class="canvas">

  <section class="card card--front">
    <div class="band band--top"></div>
    <div class="band band--bottom"></div>
    <div class="portrait" role="img" aria-label="Black and white illustration of the magician in a jacket holding a playing card"></div>

    <div class="wordmark">
      <span class="wordmark__name">VERLINDO</span>
      <span class="wordmark__sub">MAGICIEN</span>
    </div>

    <div class="person">
      <h1 class="person__name">MARC RAVOULET</h1>
      <p class="person__role">MAGICIAN</p>
    </div>

    <ul class="contacts">
      <li>
        <svg viewBox="0 0 24 24" aria-hidden="true"><path d="M6.6 10.8a15.1 15.1 0 0 0 6.6 6.6l2.2-2.2a1 1 0 0 1 1-.25 11.4 11.4 0 0 0 3.6.57 1 1 0 0 1 1 1V20a1 1 0 0 1-1 1A17 17 0 0 1 3 4a1 1 0 0 1 1-1h3.5a1 1 0 0 1 1 1c0 1.25.2 2.45.57 3.57a1 1 0 0 1-.25 1z"/></svg>
        0381 946 157
      </li>
      <li>
        <svg viewBox="0 0 24 24" aria-hidden="true"><path d="M2 9c0-2 4.5-4 10-4s10 2 10 4v2h-5V9H7v2H2z"/><path d="M6 12h12l2 7H4z"/></svg>
        0674 219 503
      </li>
      <li>
        <svg viewBox="0 0 24 24" aria-hidden="true"><path d="M2 5h20v14H2z M4 7v1l8 5 8-5V7l-8 5z" fill-rule="evenodd"/></svg>
        contact@verlindoillusions.example
      </li>
      <li>
        <svg viewBox="0 0 24 24" aria-hidden="true"><circle cx="12" cy="12" r="10"/><path d="M7 8c2 0 3 1 3 3s2 2 2 4-1 3-1 5" stroke="#fff" stroke-width="1.6" fill="none"/></svg>
        www.verlindoillusions.example
      </li>
    </ul>

    <address class="address">
      MAGICIAN VERLINDO<br>
      17 rue des Tilleuls - 25000 BESANÇON
    </address>
  </section>

  <section class="card card--back">
    <div class="portrait" role="img" aria-label="Black and white illustration of the magician in a jacket holding a playing card"></div>
    <div class="wordmark">
      <span class="wordmark__name">VERLINDO</span>
      <span class="wordmark__sub">MAGICIEN</span>
    </div>
  </section>

</main>
</body>
</html>
```